design a construction company business card

Design business card around our logo. Card must have all the typical info: name, title, address, phone, email, business name, etc. Somewhere on the card I would like to see our motto "Built on integrity... Inspired by commitment." Consider adding a splash of bright orange to the card to complement the blues and silvers/grays in the logo. We are open to metallic inks, textures, etc. We would like to see options on both light and dark backgrounds. The font in the logo is Euro Technic Extended Regular.

```html
<!DOCTYPE html>
<html lang="en">
<head>
<meta charset="utf-8">
<title>Halden Building, Inc. – Business Card</title>
<link rel="stylesheet" href="https://fonts.googleapis.com/css2?family=Maven+Pro:wght@400;600;700&display=swap">
<style>
  :root {
    --page-bg: #141516;
    --card-dark: #151618;
    --card-mid: #232427;
    --brand-blue: #2a6bc4;
    --accent-gray: #8a8b8d;
    --text-light: #e6e6e6;
    --text-soft: #a9a9ab;
  }
  * { margin: 0; padding: 0; box-sizing: border-box; }
  html, body {
    width: 1200px; height: 1000px; overflow: hidden;
    background: var(--page-bg);
    font-family: "Maven Pro", sans-serif;
  }
  .canvas { position: relative; width: 1200px; height: 1000px; }

  .card {
    position: absolute; left: 258px; width: 685px; height: 390px;
    background: radial-gradient(ellipse at 45% 40%, var(--card-mid) 0%, var(--card-dark) 70%);
    overflow: hidden;
  }
  .card-front { top: 72px; }
  .card-back { top: 540px; }

  /* Front */
  .front-brand {
    position: absolute; left: 0; right: 0; top: 200px;
    text-align: center; color: var(--brand-blue);
    font-weight: 700; font-size: 34px; letter-spacing: 1px;
  }
  .front-motto {
    position: absolute; left: 0; right: 0; top: 268px;
    text-align: center; color: var(--text-soft);
    font-size: 16.5px; letter-spacing: 0.3px;
  }

  /* Back */
  .back-brand {
    position: absolute; right: 46px; top: 100px;
    color: var(--brand-blue); font-weight: 700; font-size: 23px; letter-spacing: 0.5px;
  }
  .holder-name {
    position: absolute; left: 40px; top: 160px;
    color: var(--brand-blue); font-size: 23px; letter-spacing: 0.5px;
  }
  .holder-name .given { font-weight: 700; }
  .holder-name .family { font-weight: 400; }
  .holder-title {
    position: absolute; left: 40px; top: 188px;
    color: var(--text-light); font-size: 16px;
  }
  .holder-title .company { color: var(--brand-blue); }
  .divider {
    position: absolute; left: 40px; top: 227px; width: 599px; height: 1px;
    background: var(--brand-blue);
  }
  .contact-list { position: absolute; left: 40px; top: 246px; list-style: none; }
  .contact-list li {
    display: flex; align-items: center; height: 28px;
    color: var(--text-light); font-size: 16.5px;
  }
  .contact-list svg { width: 20px; height: 20px; margin-right: 7px; fill: var(--brand-blue); }
  .address {
    position: absolute; right: 46px; top: 245px; text-align: right;
    color: var(--text-light); font-size: 16.5px; line-height: 27px;
  }
  .footer-band { position: absolute; left: 0; bottom: 0; width: 685px; height: 13px; }
</style>
</head>
<body>
<main class="canvas">

  <section class="card card-front" aria-label="Card front">
    <div class="front-brand">HALDEN BUILDING, INC.</div>
    <p class="front-motto">Built on Integrity... Inspired by Commitment</p>
  </section>

  <section class="card card-back" aria-label="Card back">
    <div class="back-brand">HALDEN BUILDING, INC.</div>

    <h1 class="holder-name"><span class="given">MARCUS</span> <span class="family">REYES</span></h1>
    <p class="holder-title">CEO of <span class="company">Halden Building, INC</span></p>
    <div class="divider"></div>

    <ul class="contact-list">
      <li>
        <svg viewBox="0 0 24 24" aria-hidden="true"><path d="M6.6 10.8a15.1 15.1 0 0 0 6.6 6.6l2.2-2.2c.3-.3.7-.4 1-.2 1.1.4 2.3.6 3.6.6.6 0 1 .4 1 1V20c0 .6-.4 1-1 1C10.6 21 3 13.4 3 4c0-.6.4-1 1-1h3.5c.6 0 1 .4 1 1 0 1.3.2 2.5.6 3.6.1.3 0 .7-.2 1z"/></svg>
        (02) 5550 1842
      </li>
      <li>
        <svg viewBox="0 0 24 24" aria-hidden="true"><path d="M7 2h10a2 2 0 0 1 2 2v16a2 2 0 0 1-2 2H7a2 2 0 0 1-2-2V4a2 2 0 0 1 2-2zm0 3v13h10V5zm5 14.2a1 1 0 1 0 0 2 1 1 0 0 0 0-2z"/></svg>
        0400 555 214
      </li>
      <li>
        <svg viewBox="0 0 24 24" aria-hidden="true"><path d="M3 6h18v1.5l-9 5.5-9-5.5zm0 3.3 9 5.5 9-5.5V18H3z"/></svg>
        info@haldenbuilding.com
      </li>
      <li>
        <svg viewBox="0 0 24 24" aria-hidden="true"><path d="M12 2a10 10 0 1 0 0 20 10 10 0 0 0 0-20zm-1 17.9A8 8 0 0 1 4.2 10.2L9 15v1a2 2 0 0 0 2 2zm6.9-2.5A2 2 0 0 0 16 16h-1v-3a1 1 0 0 0-1-1H8v-2h2a1 1 0 0 0 1-1V7h2a2 2 0 0 0 2-2v-.4a8 8 0 0 1 2.9 12.8z"/></svg>
        www.haldenbuilding.com
      </li>
    </ul>

    <address class="address" style="font-style:normal">
      118/4 Arbor St, Westfield<br>
      NSW 2150, NY
    </address>

    <svg class="footer-band" viewBox="0 0 685 13" aria-hidden="true">
      <polygon points="0,0 459,0 454,13 0,13" fill="var(--brand-blue)"/>
      <polygon points="465,0 685,0 685,13 460,13" fill="var(--accent-gray)"/>
    </svg>
  </section>

</main>
</body>
</html>
```